Animal Eye Clinic needs a Business card

We are a new veterinary ophthalmology practice (Ridgeline Pet Vision Care) and we need a business card designed. We only see animal eyes - we are not a regular veterinary clinic. We already have a logo. We are looking for a professional, good looking business card to hand out to our clients. We are looking for something simple but professional and contemporary. Our logo is likely the only picture/graphic that needs to be on the card.
Updates

Contact Information for Business Card

Delia Vossman, BSc, DVM, MSc, DipACVO
Veterinary Ophthalmologist

Phone: 250.418.3927
Email: ridgelinepetvisioncare@mailbox-example.net
Website: ridgelinepetvisioncare-example.net
Address: 1874 Thornbury Rd
Kelowna, BC, V1X 4M9

Colors

Designer to choose colors to be used in the design.

Requirements
Must have
• Our logo (attached)

```html
<!DOCTYPE html>
<html lang="en">
<head>
<meta charset="utf-8">
<title>Ridgeline Pet Vision Care – Business Card</title>
<link href="https://fonts.googleapis.com/css2?family=Roboto:wght@300;400;700&display=swap" rel="stylesheet">
<style>
  :root {
    --teal: #0a98a8;
    --slate: #767676;
    --white: #ffffff;
    --backdrop: #d9dadb;
    --card-shadow: 0 10px 30px rgba(0,0,0,.25);
  }
  * { box-sizing: border-box; margin: 0; padding: 0; }
  html, body { width: 1200px; height: 901px; overflow: hidden; }
  body {
    background: var(--backdrop);
    font-family: "Roboto", Arial, sans-serif;
    position: relative;
  }
  .card {
    position: absolute;
    width: 600px;
    height: 343px;
    box-shadow: var(--card-shadow);
    overflow: hidden;
  }

  /* Front */
  .card-front {
    left: 60px; top: 70px;
    background: var(--teal);
    display: flex; align-items: center; justify-content: center;
  }
  .brand { display: flex; align-items: center; gap: 16px; }
  .brand-dot {
    width: 22px; height: 22px; border-radius: 50%;
    background: var(--white);
  }
  .brand-name {
    color: var(--white);
    font-weight: 700;
    font-size: 30px;
    letter-spacing: .5px;
    text-transform: uppercase;
    line-height: 1.1;
  }

  /* Back */
  .card-back {
    left: 540px; top: 488px;
    background: var(--slate);
    color: var(--white);
  }
  .brand-panel {
    position: absolute; top: 0; right: 0;
    width: 250px; height: 100%;
    background: var(--white);
    border-left: 18px solid var(--teal);
    display: flex; align-items: center; justify-content: center;
    flex-direction: column; gap: 14px;
  }
  .brand-panel .brand-dot { background: var(--teal); width: 48px; height: 48px; }
  .brand-panel .brand-name {
    color: var(--teal); font-size: 20px; text-align: center;
  }
  .contact {
    position: absolute; left: 34px; top: 34px; width: 300px;
  }
  .person-name { font-size: 20px; font-weight: 700; }
  .person-name .credentials { font-size: 12px; font-weight: 400; }
  .person-role { font-size: 14px; font-weight: 300; margin-top: 2px; }
  .address { margin-top: 48px; font-size: 14px; font-weight: 300; line-height: 1.35; }
  .links { margin-top: 48px; list-style: none; font-size: 12.5px; font-weight: 300; line-height: 1.5; }
  .links li { display: flex; align-items: center; gap: 7px; white-space: nowrap; }
  .links svg { width: 11px; height: 11px; fill: var(--white); flex: none; }
</style>
</head>
<body>

<section class="card card-front" aria-label="Card front">
  <div class="brand">
    <span class="brand-dot"></span>
    <span class="brand-name">Ridgeline<br>Pet Vision Care</span>
  </div>
</section>

<section class="card card-back" aria-label="Card back">
  <div class="contact">
    <p class="person-name">Delia Vossman<span class="credentials">, BSc, DVM, MSc, DipACVO</span></p>
    <p class="person-role">Veterinary Ophthalmologist</p>
    <p class="address">1874 Thornbury Rd<br>Kelowna, BC, V1X 4M9</p>
    <ul class="links">
      <li>
        <svg viewBox="0 0 24 24"><path d="M6.6 10.8a15.1 15.1 0 0 0 6.6 6.6l2.2-2.2a1 1 0 0 1 1-.25 11.4 11.4 0 0 0 3.6.57 1 1 0 0 1 1 1V20a1 1 0 0 1-1 1A17 17 0 0 1 3 4a1 1 0 0 1 1-1h3.5a1 1 0 0 1 1 1c0 1.25.2 2.45.57 3.6a1 1 0 0 1-.25 1z"/></svg>
        250.418.3927
      </li>
      <li>
        <svg viewBox="0 0 24 24"><path d="M2 5h20v14H2z M2 5l10 8 10-8" stroke="#767676" stroke-width="1.5"/></svg>
        ridgelinepetvisioncare@mailbox-example.net
      </li>
      <li>
        <svg viewBox="0 0 24 24"><circle cx="12" cy="12" r="10"/><path d="M2 12h20M12 2c3 3 3 17 0 20M12 2c-3 3-3 17 0 20" stroke="#767676" stroke-width="1.5" fill="none"/></svg>
        www.ridgelinepetvisioncare-example.net
      </li>
    </ul>
  </div>
  <div class="brand-panel">
    <span class="brand-dot"></span>
    <span class="brand-name">Ridgeline<br>Pet Vision Care</span>
  </div>
</section>

</body>
</html>
```